Bluecrest Learning Corps by graduating students from college in two years

Based on the logo design, create stationary and business cards for
Dr. Venrel T Oskamp, CEO, (703) 482-1736
and Marisa Deltoft, Respresentative, (301) 647-2208
Address: 4719 Pellham Court, Brenton Hills, OR 97208
Incorporate elelments of the logo

Target Market(s)

USA

Font styles to use
Other font styles liked:
• match with the logo type style

```html
<!DOCTYPE html>
<html lang="en">
<head>
<meta charset="utf-8">
<title>Bluecrest Learning Corps – Stationery</title>
<link href="https://fonts.googleapis.com/css2?family=Tinos:wght@400;700&display=swap" rel="stylesheet">
<style>
:root{
  --navy:#1f2858;
  --gold:#f8c431;
  --paper:#ffffff;
  --ground:#d6dbde;
  --rule:#c9ccd6;
  --faint:#e9e9f3;
}
*{box-sizing:border-box;margin:0;padding:0}
html,body{width:1200px;height:711px;overflow:hidden}
body{background:var(--ground);font-family:"Tinos","Times New Roman",serif;color:var(--navy);position:relative}
.piece{position:absolute;overflow:hidden}
.mark{display:flex;flex-direction:column;align-items:center;gap:3px;position:absolute;left:0;right:0}
.mark-dot{border-radius:50%;background:var(--gold);border:2px solid var(--navy)}
.mark-name{font-weight:700;white-space:nowrap;color:var(--navy)}
.on-navy .mark-name{color:var(--gold)}
.on-gold .mark-dot{background:var(--paper)}

/* business cards */
.card{width:247px;height:141px}
.card-front{background:var(--gold);left:73px;top:56px}
.card-back{background:var(--navy);left:73px}
.card-back .band{position:absolute;left:0;right:0;bottom:0;height:6px;background:var(--gold)}
.holder{position:absolute;right:132px;top:90px;text-align:right}
.holder-name{color:var(--gold);font-weight:700;font-size:11px;white-space:nowrap}
.holder-role{color:var(--paper);font-size:6.5px}
.divider{position:absolute;left:122px;top:83px;width:1px;height:28px;background:var(--gold)}
.contacts{position:absolute;left:136px;top:87px;list-style:none;color:var(--paper);font-size:6px;line-height:8.4px}
.contacts li{display:flex;align-items:center;gap:4px}
.ico{width:6px;height:6px;flex:none}
.card-address{position:absolute;left:0;right:0;top:122px;text-align:center;color:var(--gold);font-size:6px}

/* letterhead & slip */
.letterhead{left:374px;top:55px;width:320px;height:452px;background:var(--paper)}
.head-rule{position:absolute;left:17px;right:17px;top:47px;height:1px;background:var(--navy)}
.head-rule::after{content:"";position:absolute;left:50%;top:-1px;width:56px;height:2px;margin-left:-28px;background:var(--gold)}
.watermark{position:absolute;left:60px;top:128px;width:200px;height:200px;display:flex;flex-direction:column;align-items:center;justify-content:center;gap:8px}
.watermark .ring{width:120px;height:120px;border-radius:50%;border:3px solid var(--faint)}
.watermark .mark-name{color:var(--faint);font-size:14px}
.foot-rule{position:absolute;left:0;right:0;height:1px;background:var(--navy)}
.foot-address{position:absolute;left:0;right:0;text-align:center;font-size:6.3px;display:flex;justify-content:center;align-items:center;gap:4px}
.foot-contacts{position:absolute;left:0;right:0;display:flex;justify-content:space-around;padding:0 24px;font-size:6.3px}
.foot-contacts span{display:flex;align-items:center;gap:4px}
.foot-band{position:absolute;left:0;right:0;bottom:0;background:var(--gold)}
.slip{left:371px;top:523px;width:321px;height:142px;background:var(--paper)}

/* envelope */
.envelope{left:36px;top:523px;width:320px;height:142px;background:var(--paper);box-shadow:0 1px 2px rgba(0,0,0,.08)}
.flap{position:absolute;left:0;right:0;top:0;height:48px;background:var(--paper);border-bottom:1px solid #e4e6ea;border-radius:0 0 16px 16px;box-shadow:0 4px 6px rgba(0,0,0,.06)}

/* folder */
.folder-cover{left:728px;top:50px;width:120px;height:230px;background:#eceeef}
.folder-cover .band{position:absolute;left:0;right:0;bottom:0;height:10px;background:var(--gold)}
.folder-inside{left:913px;top:60px;width:228px;height:212px;background:#f1f2f3}
.folder-inside .spine{position:absolute;left:113px;top:0;width:1px;height:100%;background:#d4d7da}

/* notebook */
.notebook-cover{left:806px;top:292px;width:262px;height:156px;background:var(--gold);border-left:8px solid #b9bcc0}
.notebook-spread{left:782px;top:462px;width:274px;height:192px;background:var(--paper)}
.page{position:absolute;top:0;width:131px;height:100%}
.page-left{left:0}
.page-right{right:0}
.coil{position:absolute;left:131px;top:0;width:12px;height:100%;background:repeating-linear-gradient(to bottom,#8a8d92 0 2px,transparent 2px 5px)}
.page-title{position:absolute;left:10px;top:14px;font-size:5px;color:var(--gold)}
.page-date{position:absolute;left:10px;top:21px;font-size:3.6px;font-style:italic;color:var(--navy)}
.page-date::after{content:"";display:inline-block;width:30px;height:1px;background:var(--navy);margin-left:4px;vertical-align:middle}
.page-head{position:absolute;left:97px;right:6px;top:25px;height:1px;background:var(--navy)}
.page-lines{position:absolute;left:10px;right:6px;top:36px;bottom:8px;background:repeating-linear-gradient(to bottom,transparent 0 9px,var(--rule) 9px 10px)}
</style>
</head>
<body>

<!-- business card front -->
<section class="piece card card-front on-gold">
  <div class="mark" style="top:30px">
    <div class="mark-dot" style="width:52px;height:52px"></div>
    <div class="mark-name" style="font-size:11px">Bluecrest Learning Corps</div>
  </div>
</section>

<!-- business card: representative -->
<section class="piece card card-back on-navy" style="top:211px">
  <div class="mark" style="top:10px">
    <div class="mark-dot" style="width:36px;height:36px"></div>
    <div class="mark-name" style="font-size:7px">Bluecrest Learning Corps</div>
  </div>
  <div class="holder">
    <div class="holder-name">Marisa Deltoft</div>
    <div class="holder-role">Respresentative</div>
  </div>
  <div class="divider"></div>
  <ul class="contacts">
    <li><svg class="ico" viewBox="0 0 10 10"><path d="M2 1l2 2-1 1.5a6 6 0 0 0 2.5 2.5L7 6l2 2-1.5 1.5C4 9 1 6 .5 2.5z" fill="#fff"/></svg>(301) 647-2208</li>
    <li><svg class="ico" viewBox="0 0 10 10"><circle cx="5" cy="5" r="4" fill="none" stroke="#f8c431" stroke-width="1.4"/><path d="M1 5h8M5 1v8" stroke="#f8c431"/></svg>www.bluecrestlearning.org</li>
    <li><svg class="ico" viewBox="0 0 10 10"><rect x="1" y="2.5" width="8" height="5.5" fill="none" stroke="#f8c431" stroke-width="1.2"/><path d="M1 2.5l4 3 4-3" fill="none" stroke="#f8c431"/></svg>info@bluecrestlearning.org</li>
  </ul>
  <div class="card-address">4719 Pellham Court, Brenton Hills, OR 97208</div>
  <div class="band"></div>
</section>

<!-- business card: CEO -->
<section class="piece card card-back on-navy" style="top:366px">
  <div class="mark" style="top:10px">
    <div class="mark-dot" style="width:36px;height:36px"></div>
    <div class="mark-name" style="font-size:7px">Bluecrest Learning Corps</div>
  </div>
  <div class="holder">
    <div class="holder-name">Dr. Venrel T Oskamp</div>
    <div class="holder-role">CEO</div>
  </div>
  <div class="divider"></div>
  <ul class="contacts">
    <li><svg class="ico" viewBox="0 0 10 10"><path d="M2 1l2 2-1 1.5a6 6 0 0 0 2.5 2.5L7 6l2 2-1.5 1.5C4 9 1 6 .5 2.5z" fill="#fff"/></svg>(703) 482-1736</li>
    <li><svg class="ico" viewBox="0 0 10 10"><circle cx="5" cy="5" r="4" fill="none" stroke="#f8c431" stroke-width="1.4"/><path d="M1 5h8M5 1v8" stroke="#f8c431"/></svg>www.bluecrestlearning.org</li>
    <li><svg class="ico" viewBox="0 0 10 10"><rect x="1" y="2.5" width="8" height="5.5" fill="none" stroke="#f8c431" stroke-width="1.2"/><path d="M1 2.5l4 3 4-3" fill="none" stroke="#f8c431"/></svg>info@bluecrestlearning.org</li>
  </ul>
  <div class="card-address">4719 Pellham Court, Brenton Hills, OR 97208</div>
  <div class="band"></div>
</section>

<!-- envelope -->
<section class="piece envelope">
  <div class="flap"></div>
  <div class="mark" style="top:8px">
    <div class="mark-dot" style="width:22px;height:22px"></div>
    <div class="mark-name" style="font-size:6px">Bluecrest Learning Corps</div>
  </div>
</section>

<!-- letterhead -->
<section class="piece letterhead">
  <div class="mark" style="top:8px">
    <div class="mark-dot" style="width:24px;height:24px"></div>
    <div class="mark-name" style="font-size:6px">Bluecrest Learning Corps</div>
  </div>
  <div class="head-rule"></div>
  <div class="watermark">
    <div class="ring"></div>
    <div class="mark-name">Bluecrest Learning Corps</div>
  </div>
  <div class="foot-rule" style="top:408px"></div>
  <div class="foot-address" style="top:414px">
    <svg class="ico" viewBox="0 0 10 10"><path d="M5 9.5S1.5 5.5 1.5 3.5a3.5 3.5 0 0 1 7 0C8.5 5.5 5 9.5 5 9.5z" fill="#f8c431"/><circle cx="5" cy="3.5" r="1.2" fill="#fff"/></svg>
    4719 Pellham Court, Brenton Hills, OR 97208
  </div>
  <div class="foot-contacts" style="top:426px">
    <span><svg class="ico" viewBox="0 0 10 10"><path d="M2 1l2 2-1 1.5a6 6 0 0 0 2.5 2.5L7 6l2 2-1.5 1.5C4 9 1 6 .5 2.5z" fill="#f8c431"/></svg>(703) 482-1736</span>
    <span><svg class="ico" viewBox="0 0 10 10"><rect x="1" y="2.5" width="8" height="5.5" fill="none" stroke="#f8c431" stroke-width="1.2"/><path d="M1 2.5l4 3 4-3" fill="none" stroke="#f8c431"/></svg>info@bluecrestlearning.org</span>
    <span><svg class="ico" viewBox="0 0 10 10"><circle cx="5" cy="5" r="4" fill="none" stroke="#f8c431" stroke-width="1.4"/><path d="M1 5h8M5 1v8" stroke="#f8c431"/></svg>www.bluecrestlearning.org</span>
  </div>
  <div class="foot-band" style="height:9px"></div>
</section>

<!-- compliment slip -->
<section class="piece slip">
  <div class="mark" style="top:16px">
    <div class="mark-dot" style="width:52px;height:52px"></div>
    <div class="mark-name" style="font-size:8px">Bluecrest Learning Corps</div>
  </div>
  <div class="foot-rule" style="top:105px"></div>
  <div class="foot-address" style="top:111px">
    <svg class="ico" viewBox="0 0 10 10"><path d="M5 9.5S1.5 5.5 1.5 3.5a3.5 3.5 0 0 1 7 0C8.5 5.5 5 9.5 5 9.5z" fill="#f8c431"/><circle cx="5" cy="3.5" r="1.2" fill="#fff"/></svg>
    4719 Pellham Court, Brenton Hills, OR 97208
  </div>
  <div class="foot-contacts" style="top:122px">
    <span><svg class="ico" viewBox="0 0 10 10"><path d="M2 1l2 2-1 1.5a6 6 0 0 0 2.5 2.5L7 6l2 2-1.5 1.5C4 9 1 6 .5 2.5z" fill="#f8c431"/></svg>(703) 482-1736</span>
    <span><svg class="ico" viewBox="0 0 10 10"><rect x="1" y="2.5" width="8" height="5.5" fill="none" stroke="#f8c431" stroke-width="1.2"/><path d="M1 2.5l4 3 4-3" fill="none" stroke="#f8c431"/></svg>info@bluecrestlearning.org</span>
    <span><svg class="ico" viewBox="0 0 10 10"><circle cx="5" cy="5" r="4" fill="none" stroke="#f8c431" stroke-width="1.4"/><path d="M1 5h8M5 1v8" stroke="#f8c431"/></svg>www.bluecrestlearning.org</span>
  </div>
  <div class="foot-band" style="height:6px"></div>
</section>

<!-- presentation folder: cover -->
<section class="piece folder-cover">
  <div class="mark" style="top:50px">
    <div class="mark-dot" style="width:96px;height:96px;border-width:3px"></div>
    <div class="mark-name" style="font-size:7px">Bluecrest Learning Corps</div>
  </div>
  <div class="band"></div>
</section>

<!-- presentation folder: inside pockets -->
<section class="piece folder-inside">
  <div class="spine"></div>
  <svg style="position:absolute;left:0;top:0" width="228" height="212" viewBox="0 0 228 212">
    <path d="M0 142 L70 142 Q113 142 113 185 L113 212 L0 212Z" fill="#1f2858"/>
    <path d="M114 185 Q114 142 157 142 L228 142 L228 212 L114 212Z" fill="#f8c431"/>
  </svg>
  <div class="mark" style="top:162px;left:0;right:114px">
    <div class="mark-dot" style="width:22px;height:22px"></div>
    <div class="mark-name" style="font-size:5px;color:#f8c431">Bluecrest Learning Corps</div>
  </div>
  <div class="mark" style="top:162px;left:114px;right:0">
    <div class="mark-dot" style="width:22px;height:22px;background:#fff"></div>
    <div class="mark-name" style="font-size:5px">Bluecrest Learning Corps</div>
  </div>
</section>

<!-- notebook cover -->
<section class="piece notebook-cover on-gold">
  <div class="mark" style="top:22px">
    <div class="mark-dot" style="width:86px;height:86px;border-width:3px"></div>
    <div class="mark-name" style="font-size:10px">Bluecrest Learning Corps</div>
  </div>
</section>

<!-- notebook pages -->
<section class="piece notebook-spread">
  <div class="page page-left">
    <div class="page-title">Notes</div>
    <div class="page-date">Date Of</div>
    <div class="mark-dot" style="position:absolute;left:106px;top:6px;width:16px;height:16px;border-width:1.5px"></div>
    <div class="page-head"></div>
    <div class="page-lines"></div>
  </div>
  <div class="coil"></div>
  <div class="page page-right">
    <div class="page-title">Notes</div>
    <div class="page-date">Date Of</div>
    <div class="mark-dot" style="position:absolute;left:106px;top:6px;width:16px;height:16px;border-width:1.5px"></div>
    <div class="page-head"></div>
    <div class="page-lines"></div>
  </div>
</section>

</body>
</html>
```